Package of web graphics needed

Utilizing a recently selected logo from a Pixel Harbor contest, we need to have some ads, fb cover, home page slide image created for our new 844-Toll-Free Number Product. Please feel free to check our site at www.vantaquickline.com

You'll find attached the 844 toll free logo in 2 layouts.

Here are the ads and dimensions of each that are needed:
1.)Banners/ads - 468x60
468×60 px
125×125 px
120×600 px
120x90 px
88×31 px button
5.)FB Cover - 851 x 315
6.)Home page slider image - 944 x 328

Here is the text & some ideas to use for these. Feel free to use different versions depending on which ad they work better on:
-

Market Your Business in a Memorable Way – Pre-Order Yours Today, Deadline: Dec. 7th
[include logo]
-
[844 logo] Don't Miss out on your chance to finally get a great vanity!

Order Yours Today
-

Don't Miss out on your chance to finally get a great vanity!
Dec. 7th Deadline to pre-order

Don't Ignore 844!– The newest toll free prefix – Coming Dec. 7th – Get Yours Today

FB COVER guidelines -
Requirements:
Include the logo
Limited Time Left – Get your Reservation in by December 7th

HOME PAGE Image Slide:
Use the logo,

Couple of Ideas we're interested in seeing:

[Billboard sign stock image … with the number 877-Ring-YES on the billboard]
[844 logo and caricature] [1 caricature looking surprised]

Reason: Need more designs to review !

```html
<!DOCTYPE html>
<html lang="en">
<head>
<meta charset="utf-8">
<title>877 Ring Yes – Home Page Slide</title>
<link rel="stylesheet" href="https://fonts.googleapis.com/css2?family=Montserrat:wght@700;800&family=Fira+Sans+Condensed:wght@600&family=Kalam:wght@400&display=swap">
<style>
  :root {
    --page-bg: #222222;
    --sky-light: #cfe9fb;
    --sky-mid: #4aa8ea;
    --sky-deep: #1a78d2;
    --navy: #0d3466;
    --green: #6cbd45;
    --green-dark: #48a023;
    --panel-white: #ffffff;
    --frame-grey: #b9bec4;
    --stand-tone: #8fb8de;
  }
  * { box-sizing: border-box; margin: 0; padding: 0; }
  html, body {
    width: 1200px; height: 750px; overflow: hidden;
    background: var(--page-bg);
  }
  .slide {
    position: absolute; left: 128px; top: 211px;
    width: 944px; height: 328px; overflow: hidden;
    background: linear-gradient(160deg, var(--sky-deep) 0%, var(--sky-mid) 45%, var(--sky-light) 80%, var(--sky-mid) 100%);
  }
  .skyline {
    position: absolute; left: 0; bottom: 0; width: 944px; height: 200px;
    background: linear-gradient(180deg, rgba(120,190,240,0) 0%, rgba(60,150,225,0.55) 50%, rgba(25,110,200,0.8) 100%);
  }
  .billboard-stand {
    position: absolute; left: 24px; top: 268px; width: 680px; height: 60px;
    background: linear-gradient(180deg, var(--stand-tone) 0%, rgba(143,184,222,0.4) 100%);
  }
  .billboard {
    position: absolute; left: 24px; top: 41px; width: 676px; height: 224px;
    background: var(--frame-grey); padding: 5px;
    box-shadow: 0 2px 6px rgba(0,0,0,0.25);
  }
  .billboard-face {
    width: 100%; height: 100%;
    background: linear-gradient(180deg, #ffffff 0%, #f1f2f4 100%);
    position: relative;
  }
  .billboard-number {
    position: absolute; left: 28px; top: 36px; width: 402px; height: 140px;
    display: flex; align-items: center; justify-content: center;
    font-family: "Montserrat", sans-serif; font-weight: 800;
    font-size: 124px; line-height: 1; color: var(--navy); letter-spacing: 10px;
  }
  .headline {
    position: absolute; left: 445px; top: 30px;
    font-family: "Montserrat", sans-serif; font-weight: 800;
    font-size: 64px; line-height: 60px; letter-spacing: 1px;
  }
  .headline .ring { display: block; color: var(--navy); }
  .headline .yes { display: block; color: var(--green); }
  .tagline {
    position: absolute; left: 34px; top: 180px;
    font-family: "Montserrat", sans-serif; font-weight: 700;
    font-size: 21px; color: var(--green); letter-spacing: 1px;
  }
  .brand-card {
    position: absolute; left: 742px; top: 38px; width: 166px; height: 116px;
    background: var(--panel-white);
    display: flex; align-items: center; justify-content: center; gap: 8px;
    padding: 10px;
  }
  .brand-card .brand-dot { width: 12px; height: 12px; background: var(--green); flex: none; }
  .brand-card .brand-name {
    font-family: "Montserrat", sans-serif; font-weight: 800;
    font-size: 19px; line-height: 22px; color: var(--navy);
  }
  .order-button {
    position: absolute; left: 745px; top: 166px; width: 163px; height: 72px;
    border: 3px solid #bfe6a6; border-radius: 4px;
    background: linear-gradient(180deg, #7fcc4f 0%, var(--green-dark) 100%);
    font-family: "Fira Sans Condensed", sans-serif; font-weight: 600;
    color: #fff; font-size: 23px; line-height: 25px; text-align: center;
    display: flex; align-items: center; justify-content: center;
    text-shadow: 0 1px 2px rgba(0,0,0,0.35);
  }
  .deadline {
    position: absolute; left: 745px; top: 248px; width: 163px;
    font-family: "Kalam", cursive; font-size: 21px; line-height: 25px;
    color: #fff; text-align: center;
    text-shadow: 0 1px 2px rgba(0,0,0,0.3);
  }
  .deadline sup { font-size: 11px; }
</style>
</head>
<body>
  <div class="slide">
    <div class="skyline" role="img" aria-label="Soft blue city skyline behind the billboard"></div>
    <div class="billboard-stand" role="img" aria-label="Billboard lamps, catwalk railing and support pole"></div>

    <div class="billboard">
      <div class="billboard-face">
        <div class="billboard-number">877</div>
        <h1 class="headline"><span class="ring">RING</span><span class="yes">YES</span></h1>
        <p class="tagline">MARKET YOUR BUSINESS IN A MEMORABLE WAY</p>
      </div>
    </div>

    <div class="brand-card">
      <span class="brand-dot"></span>
      <span class="brand-name">Vanta<br>Quickline</span>
    </div>

    <div class="order-button">ORDER YOURS<br>TODAY!</div>

    <p class="deadline">Deadline<br>December 7<sup>th</sup></p>
  </div>
</body>
</html>
```